Norrell Advisory WA Business Card

Create an interesting, eye catching and colourful two sided business card. We are a business consulting operation assisting SME's improve all areas of their business. We provide consulting services to assist SME's to create a culture of continuous improvement, making a positive difference in the business. Our tag line is Small changes, big rewards. We want to create a well recognised, innovative brand that can be continued throughout our website, social media and email correspondence.

Target Market(s)

Small to Medium Enterprise Business Owners

Industry/Entity Type

Business Consultant

Contact Information for Business Card

Name of Business: Norrell Advisory - Small Changes Big Rewards
Derek Holloway Ph 0407385510 Megan Holloway Ph 0407913847
Email norrelladvisorywa@mailbox-example.com
Web address TBA
FaceBook page TBA

BACKSIDE OF CARD

Providing assistance with:

• Organisation & Efficiency
• Revenue generation & Marketing
• Financial Management
• Production quality & delivery
• Systems & Process documentation
• Exit Strategy

Font styles to use
Other font styles liked:
• Calibri

Colors

Designer to choose colors to be used in the design.

Requirements
Must have
• Calibri font

```html
<!DOCTYPE html>
<html lang="en">
<head>
<meta charset="utf-8">
<title>Norrell Advisory WA Business Card</title>
<link href="https://fonts.googleapis.com/css2?family=Open+Sans:wght@400;600;700&display=swap" rel="stylesheet">
<style>
  :root {
    --stage: #dcdcdc;
    --card-white: #ffffff;
    --ink: #2b2b2b;
    --brand-green: #8dc63f;
    --brand-red: #ef4136;
    --brand-blue: #1f8ad0;
    --brand-yellow: #fbb034;
  }
  * { box-sizing: border-box; margin: 0; padding: 0; }
  html, body { width: 1200px; height: 900px; overflow: hidden; }
  body {
    background: var(--stage);
    font-family: "Open Sans", Arial, sans-serif;
    position: relative;
  }
  .card {
    position: absolute;
    width: 540px;
    height: 310px;
    border-radius: 24px;
    overflow: hidden;
  }
  /* Back side */
  .card-back {
    left: 70px;
    top: 110px;
    background: linear-gradient(172deg,
      var(--brand-green) 0%,
      var(--brand-red) 30%,
      var(--brand-blue) 65%,
      var(--brand-yellow) 100%);
    color: #fff;
    display: flex;
    flex-direction: column;
    align-items: center;
    justify-content: center;
    text-align: center;
    text-transform: uppercase;
  }
  .services-heading {
    font-size: 17px;
    font-weight: 600;
    letter-spacing: 0.5px;
    margin-bottom: 16px;
  }
  .services-list { list-style: none; }
  .services-list li {
    font-size: 14px;
    line-height: 21px;
    letter-spacing: 0.4px;
  }
  /* Front side */
  .card-front {
    left: 590px;
    top: 480px;
    background: var(--card-white);
  }
  .colour-strip {
    position: absolute;
    left: 0; right: 0; bottom: 0;
    height: 8px;
    display: flex;
  }
  .colour-strip span { flex: 1; }
  .strip-yellow { background: var(--brand-yellow); }
  .strip-blue { background: var(--brand-blue); }
  .strip-red { background: var(--brand-red); }
  .strip-green { background: var(--brand-green); }
  .brand {
    position: absolute;
    right: 34px;
    top: 46px;
    display: flex;
    align-items: center;
    gap: 10px;
    font-size: 22px;
    font-weight: 600;
    color: var(--ink);
  }
  .brand-mark {
    width: 20px; height: 20px;
    border-radius: 50%;
    background: var(--brand-blue);
  }
  .contact-list {
    position: absolute;
    right: 34px;
    top: 110px;
    list-style: none;
  }
  .contact-list li {
    display: flex;
    align-items: center;
    gap: 6px;
    font-size: 13px;
    line-height: 21px;
    color: var(--ink);
  }
  .contact-list svg { width: 13px; height: 13px; flex: none; }
  .people {
    position: absolute;
    left: 34px;
    bottom: 26px;
  }
  .person-name {
    font-size: 21px;
    font-weight: 700;
    color: var(--ink);
    text-transform: uppercase;
    line-height: 24px;
  }
  .person-phone {
    font-size: 14px;
    line-height: 20px;
    color: var(--ink);
    margin-bottom: 6px;
  }
  .person-phone:last-child { margin-bottom: 0; }
  .phone-label { color: var(--brand-blue); font-weight: 700; }
</style>
</head>
<body>

<section class="card card-back" aria-label="Business card back">
  <h2 class="services-heading">Providing assistance with:</h2>
  <ul class="services-list">
    <li>Organisation &amp; Efficiency</li>
    <li>Revenue Generation &amp; Marketing</li>
    <li>Financial Management</li>
    <li>Production Quality &amp; Delivery</li>
    <li>Systems &amp; Process Documentation</li>
    <li>Exit Strategy</li>
  </ul>
</section>

<section class="card card-front" aria-label="Business card front">
  <div class="brand"><span class="brand-mark"></span>Norrell Advisory</div>

  <ul class="contact-list">
    <li>
      <svg viewBox="0 0 14 14" aria-hidden="true"><rect x="0.5" y="2.5" width="13" height="9" rx="1" fill="var(--brand-blue)"/><path d="M1 3l6 5 6-5" fill="none" stroke="#fff" stroke-width="1.2"/></svg>
      norrelladvisorywa@mailbox-example.com
    </li>
    <li>
      <svg viewBox="0 0 14 14" aria-hidden="true"><circle cx="7" cy="7" r="6.5" fill="var(--brand-blue)"/><ellipse cx="7" cy="7" rx="2.6" ry="6" fill="none" stroke="#fff" stroke-width="1"/><path d="M1 7h12" stroke="#fff" stroke-width="1"/></svg>
      www.norrelladvisory-example.com
    </li>
    <li>
      <svg viewBox="0 0 14 14" aria-hidden="true"><circle cx="7" cy="7" r="6.5" fill="var(--brand-blue)"/></svg>
      social-example.com/norrelladvisory
    </li>
  </ul>

  <div class="people">
    <p class="person-name">Derek Holloway</p>
    <p class="person-phone"><span class="phone-label">M:</span> 0407385510</p>
    <p class="person-name">Megan Holloway</p>
    <p class="person-phone"><span class="phone-label">M:</span> 0407913847</p>
  </div>

  <div class="colour-strip" aria-hidden="true">
    <span class="strip-yellow"></span>
    <span class="strip-blue"></span>
    <span class="strip-red"></span>
    <span class="strip-green"></span>
  </div>
</section>

</body>
</html>
```